International Petrochemical business needs a web design for Clearway Desk system

We need a web design for a "Clearway Desk" system for an international petrochemical company. The web site is used internally within the company. It is hosted by an internal department which provides government permit request service for other departments.

We would like to see designs of two pages using color light blue. (home page, internal page as attached).
Home Page:
1. Header has a background image and small animation. Header on home page can be taller than the header of the internal page.
2. Layout as attached.

Internal Page:
1. Header can use the same background image as the home page and can be shorter to utilize the page for content.
2. The blue icon behind every captions represent an icon. When user move mouse over this icon, it displays the caption in Thai language as a tooltip. This icon needs to be redesign.

The final design should communicate the followings:
- Excellent service provided system in terms of time and accurary
- Rapid growth of business via building petrochemical refinery plant
Updates

For Internal Page, the blue circle behind every captions represent an icon. When mouse over this icon, a tool tip showing the caption in Thai language is shown. Please also design this icon..

There are more feedbacks from customer as followed:

1. Banner should consists of 
    1.1 "Approved" stamp on paper
    1.2 An image of Garuda. It is used on every government documents in Thailand
    1.3 Image of petrochemical plant
2. Each menu item (Home, Permit, Search, etc) should have different colors. Drop down menu will use the same color as its parent menu item.
3. Overall tone of the web page should be light blue with background of the body the web page in white
4. "New Request" button should use green color with icon on it
5. Table header of each box in the body of the page should use dark blue background with text in white

Please kindly submit your revisions.
Thank you.

Industry/Entity Type

Business

Requirements
Must have
• 1. Design for 1024x768 screen resolution
2. Use light blue theme
3. Background of header where the company logo is must have white background

```html
<!DOCTYPE html>
<html lang="en">
<head>
<meta charset="utf-8">
<title>Clearway Desk</title>
<link href="https://fonts.googleapis.com/css2?family=Ubuntu:wght@400;500;700&family=Arimo:wght@400;700&display=swap" rel="stylesheet">
<style>
:root{
  --navy:#13335f;
  --brand:#1a8fd6;
  --panel-top:#1e86cf;
  --panel-bottom:#0a5ba8;
  --panel-body:#eef6fc;
  --panel-border:#c9d7e2;
  --divider:#7fb3d9;
  --ink:#1b1f24;
  --link:#2f6fd6;
  --footer:#0f5a9e;
  --tab-home:#5fb7c8;
  --tab-home-drop:#2b8797;
  --tab-permits:#5cc46e;
  --tab-search:#e0b43c;
  --tab-report:#c9535a;
  --tab-admin:#7aa271;
  --tab-help:#7b3fb0;
  --go-top:#5cc95a;
  --go-bottom:#23921f;
}
*{box-sizing:border-box;margin:0;padding:0}
html,body{width:1109px;height:1200px;overflow:hidden;background:#fff}
body{font-family:"Arimo",Arial,sans-serif;color:var(--ink)}
.page{position:relative;width:1000px;height:1082px;transform:scale(1.109);transform-origin:0 0;background:#fff}
.topline{position:absolute;left:0;top:0;width:1000px;height:4px;background:var(--footer)}
.brand{position:absolute;left:44px;top:26px;display:flex;align-items:center;gap:8px}
.brand-dot{width:30px;height:30px;border-radius:50%;background:var(--brand)}
.brand-name{font-family:"Ubuntu",sans-serif;font-weight:700;font-size:18px;color:var(--brand)}
.site-title{position:absolute;right:40px;top:32px;font-family:"Ubuntu",sans-serif;font-weight:700;font-size:34px;letter-spacing:.5px;color:var(--navy)}
.nav{position:absolute;top:82px;left:0;width:1000px;height:30px}
.tab{position:absolute;top:0;width:88px;height:30px;border-radius:5px 5px 0 0;color:#fff;font-family:"Ubuntu",sans-serif;font-size:14px;text-align:center;line-height:31px;box-shadow:inset 0 1px 0 rgba(255,255,255,.4)}
.tab-home{left:375px;background:var(--tab-home)}
.tab-permits{left:475px;background:var(--tab-permits)}
.tab-search{left:576px;background:var(--tab-search)}
.tab-report{left:677px;background:var(--tab-report)}
.tab-admin{left:777px;background:var(--tab-admin)}
.tab-help{left:877px;background:var(--tab-help)}
.banner{position:absolute;left:0;top:112px;width:1000px;height:238px;
  background:linear-gradient(100deg,#1c3347 0%,#3f5a6e 30%,#7d8f9b 52%,#4d5f6c 72%,#b8b7ad 100%)}
.dropdown{position:absolute;left:375px;top:113px;width:133px;z-index:2;background:var(--tab-home-drop)}
.dropdown a{display:block;height:26px;line-height:26px;padding-left:11px;color:#fff;font-family:"Ubuntu",sans-serif;font-size:11px;text-decoration:none;border-bottom:1px solid #7cc4cf}
.panel{position:absolute;background:var(--panel-body);border:1px solid var(--panel-border);border-radius:4px;box-shadow:0 1px 3px rgba(0,0,0,.12);overflow:hidden}
.panel-head{height:44px;background:linear-gradient(var(--panel-top),var(--panel-bottom));color:#fff;font-family:"Ubuntu",sans-serif;font-weight:500;font-size:17px;line-height:46px;padding-left:13px;letter-spacing:.3px}
.cols{display:grid;margin-top:12px}
.col{padding-left:13px;border-left:1px solid var(--divider)}
.col:first-child{border-left:none}
.col h3{font-family:"Ubuntu",sans-serif;font-weight:500;font-size:15px;color:var(--ink);height:25px;letter-spacing:.3px}
.col ul{list-style:none;font-size:11.5px;line-height:18px}
.col a{color:var(--link)}
.pager{position:absolute;bottom:8px;left:50%;transform:translateX(-50%);display:flex;border:1px solid #c9d3dc;border-radius:3px;background:#fff}
.pager span{width:28px;height:22px;line-height:22px;text-align:center;font-size:13px;color:var(--link);border-left:1px solid #dfe5ea}
.pager span:first-child{border-left:none;background:#eeeeee;color:#888}
.due{display:flex;align-items:center;gap:6px}
.new-request{position:absolute;left:511px;top:766px;width:456px;height:54px;border-radius:8px;border:1px solid #1f7d1b;
  background:linear-gradient(var(--go-top),var(--go-bottom));display:flex;align-items:center;justify-content:center;gap:12px;
  color:#fff;font-family:"Ubuntu",sans-serif;font-weight:700;font-size:22px;letter-spacing:.6px}
.footer{position:absolute;left:0;top:1030px;width:1000px;height:52px;background:var(--footer);color:#fff;font-size:9.5px;display:flex;justify-content:space-between;align-items:center;padding:0 48px 0 47px}
</style>
</head>
<body>
<div class="page">
  <div class="topline"></div>
  <div class="brand"><span class="brand-dot"></span><span class="brand-name">Northbay Petrochem</span></div>
  <div class="site-title">CLEARWAY DESK</div>
  <nav class="nav">
    <div class="tab tab-home">HOME</div>
    <div class="tab tab-permits">PERMITS</div>
    <div class="tab tab-search">SEARCH</div>
    <div class="tab tab-report">REPORT</div>
    <div class="tab tab-admin">ADMIN</div>
    <div class="tab tab-help">HELP</div>
  </nav>
  <div class="banner" role="img" aria-label="Petrochemical plant pipework at night with a national emblem and an approved stamp"></div>
  <div class="dropdown">
    <a href="#">Create New Permit</a>
    <a href="#">Transfer Role</a>
    <a href="#">Transfer Res. Person</a>
  </div>

  <section class="panel" style="left:30px;top:360px;width:457px;height:198px">
    <div class="panel-head">New Requests</div>
    <div class="cols" style="grid-template-columns:149px 159px 1fr;height:101px">
      <div class="col"><h3>Request No.</h3><ul><li><a href="#">56-0003</a></li><li><a href="#">56-0004</a></li></ul></div>
      <div class="col" style="padding-left:19px"><h3>Requested Date</h3><ul><li>20/4/2013</li><li>21/4/2013</li></ul></div>
      <div class="col" style="padding-left:19px"><h3>Branch</h3><ul><li>GC1</li><li>GC2</li></ul></div>
    </div>
    <div class="pager"><span>1</span><span>2</span><span>3</span><span>4</span></div>
  </section>

  <section class="panel" style="left:509px;top:360px;width:457px;height:198px">
    <div class="panel-head">My Working Requests</div>
    <div class="cols" style="grid-template-columns:148px 159px 1fr;height:101px">
      <div class="col"><h3>Request No.</h3><ul><li><a href="#">56-0003</a></li><li><a href="#">56-0004</a></li><li><a href="#">56-0005</a></li><li><a href="#">56-0006</a></li></ul></div>
      <div class="col" style="padding-left:19px"><h3>Requested Date</h3><ul><li>20/4/2013</li><li>21/4/2013</li><li>20/4/2013</li><li>21/4/2013</li></ul></div>
      <div class="col" style="padding-left:15px"><h3>Status</h3><ul><li>Waiting for process</li><li>In progress</li><li>Incomplete document</li><li>Cancel requested</li></ul></div>
    </div>
    <div class="pager"><span>1</span><span>2</span><span>3</span><span>4</span></div>
  </section>

  <section class="panel" style="left:30px;top:570px;width:936px;height:184px">
    <div class="panel-head">Expiring Permits</div>
    <div class="cols" style="grid-template-columns:149px 159px 159px 159px 158px 1fr;height:92px">
      <div class="col"><h3>Permit No</h3><ul style="margin-top:12px"><li><a href="#">AB56001</a></li><li><a href="#">BIO5502</a></li></ul></div>
      <div class="col" style="padding-left:15px"><h3>Expire Date</h3><ul style="margin-top:12px"><li>25/3/2013</li><li>24/3/2013</li></ul></div>
      <div class="col" style="padding-left:17px"><h3>Permit Name</h3><ul style="margin-top:12px"><li>Permit Name ###10</li><li>Permit Name ###20</li></ul></div>
      <div class="col" style="padding-left:20px"><h3>Branch</h3><ul style="margin-top:12px;padding-left:3px"><li>GC1</li><li>GC2</li></ul></div>
      <div class="col" style="padding-left:14px"><h3 style="line-height:18px;height:37px">Required Time<br>(Day)</h3><ul><li>30</li><li>60</li></ul></div>
      <div class="col"><h3>Due Date</h3><ul style="margin-top:12px;padding-left:7px">
        <li class="due"><svg width="13" height="13" viewBox="0 0 13 13"><circle cx="6.5" cy="6.5" r="6" fill="#e32626"/><circle cx="5" cy="4.5" r="2" fill="#ff9a9a"/></svg>-40</li>
        <li class="due"><svg width="13" height="13" viewBox="0 0 13 13"><circle cx="6.5" cy="6.5" r="6" fill="#f2be11"/><circle cx="5" cy="4.5" r="2" fill="#ffe68a"/></svg>-15</li>
      </ul></div>
    </div>
    <div class="pager"><span>1</span><span>2</span><span>3</span><span>4</span></div>
  </section>

  <section class="panel" style="left:30px;top:766px;width:457px;height:249px">
    <div class="panel-head">My In Progress Requests</div>
    <div class="cols" style="grid-template-columns:149px 159px 1fr;height:156px">
      <div class="col"><h3>Request No.</h3><ul><li><a href="#">56-0001</a></li><li><a href="#">56-0002</a></li></ul></div>
      <div class="col" style="padding-left:19px"><h3>Requested Date</h3><ul><li>20/4/2013</li><li>21/4/2013</li></ul></div>
      <div class="col" style="padding-left:19px"><h3>Status</h3><ul><li>ระหว่างดำเนินการ</li><li>รอดำเนินการ</li></ul></div>
    </div>
    <div class="pager"><span>1</span><span>2</span><span>3</span><span>4</span></div>
  </section>

  <a class="new-request" href="#">
    <svg width="40" height="34" viewBox="0 0 40 34" aria-hidden="true">
      <rect x="2" y="8" width="16" height="20" rx="2" fill="#fff" transform="rotate(-35 10 18)"/>
      <path d="M16 22 L32 6 L37 11 L21 27 L14 29 Z" fill="#fff"/>
      <path d="M20 31 H38" stroke="#fff" stroke-width="2.5"/>
    </svg>
    NEW REQUEST
  </a>

  <section class="panel" style="left:511px;top:830px;width:456px;height:185px">
    <div class="panel-head">Recent Completed Requests</div>
    <div class="cols" style="grid-template-columns:226px 1fr;height:92px">
      <div class="col" style="padding-left:11px"><h3>Request No.</h3><ul><li><a href="#">55-0100</a></li><li><a href="#">55-0088</a></li><li><a href="#">55-0002</a></li></ul></div>
      <div class="col" style="padding-left:14px"><h3>Completed Date</h3><ul style="padding-left:4px"><li>25/3/2013</li><li>24/3/2013</li><li>18/1/2013</li></ul></div>
    </div>
    <div class="pager"><span>1</span><span>2</span><span>3</span><span>4</span></div>
  </section>

  <footer class="footer">
    <span>Copyright © 2013 NorthbayPetrochem. All rights reserved.</span>
    <span>Terms and Condition | Privacy</span>
  </footer>
</div>
</body>
</html>
```